Advertising company unique advertising platform

we need a logo design for a new company based in Australia Melbourne. We develop innovated advertising platform where consumer can use this platform to get regular discount, as business owner they can use this platform for free advertisement. Payment for this advertisement platform only payable every two weeks, when I generate revenue for their business

Industry/Entity Type

Advertising

Contact Information for Business Card

Dale Morven | Co-Founder |Managing Director
Suite 718 240 Wattlebrook Lane Melbourne Vic 3000

ABN 38 614 207 923
Tel: +61 0487 259 318 | Email: dale.morven@plivorantu.com

Font styles to use
Decorative
Script

Requirements
Must have
• Try few different design and some round corner business card
Should not have
• One round corner business card...try 4 different colour background not only black, make sure two side is designed. Be creative so imagine you are giving this to a client make sure has wow factor, if you can also try one design with engrave like all the logo, words look 3d feel
• The word Advertising Platform use attached file font

```html
<!DOCTYPE html>
<html lang="en">
<head>
<meta charset="utf-8">
<title>Brightlane Exchange — Business Card</title>
<link rel="stylesheet" href="https://fonts.googleapis.com/css2?family=Marcellus&family=Work+Sans:wght@400;500&display=swap">
<style>
  :root {
    --backdrop: #e6e6e4;
    --card-dark: #262626;
    --card-light: #ffffff;
    --accent: #f47a20;
    --ink: #2b2b2b;
    --muted: #555555;
    --rule: #333333;
  }
  * { box-sizing: border-box; margin: 0; padding: 0; }
  html, body {
    width: 1200px;
    height: 859px;
    overflow: hidden;
    background: var(--backdrop);
  }
  .stage {
    width: 1200px;
    height: 859px;
    display: flex;
    flex-direction: column;
    align-items: center;
    justify-content: center;
    gap: 40px;
  }
  .card {
    width: 620px;
    height: 354px;
    position: relative;
    box-shadow: 0 6px 18px rgba(0,0,0,0.18);
  }
  .card--back {
    background: var(--card-dark);
    display: flex;
    align-items: center;
    justify-content: center;
  }
  .brand {
    display: flex;
    align-items: center;
    gap: 14px;
    font-family: "Work Sans", sans-serif;
    font-weight: 500;
    color: var(--accent);
  }
  .brand__dot {
    border-radius: 50%;
    background: var(--accent);
    flex: none;
  }
  .card--back .brand { font-size: 34px; }
  .card--back .brand__dot { width: 42px; height: 42px; }

  .card--front { background: var(--card-light); }
  .card--front .brand {
    position: absolute;
    top: 40px;
    right: 36px;
    font-size: 20px;
    gap: 10px;
  }
  .card--front .brand__dot { width: 26px; height: 26px; }
  .abn {
    position: absolute;
    top: 82px;
    right: 36px;
    font-family: "Work Sans", sans-serif;
    font-size: 13px;
    color: var(--ink);
    letter-spacing: 0.5px;
  }
  .abn__label { color: var(--accent); }

  .rule {
    position: absolute;
    height: 1px;
    background: var(--rule);
  }
  .rule--top { top: 182px; left: 250px; right: 40px; }
  .rule--bottom { top: 262px; left: 36px; right: 40px; }

  .person {
    position: absolute;
    top: 196px;
    left: 36px;
    font-family: "Marcellus", serif;
  }
  .person__name {
    font-size: 31px;
    font-weight: 400;
    color: var(--accent);
    letter-spacing: 1px;
    line-height: 1.05;
    text-transform: uppercase;
  }
  .person__role {
    font-size: 11px;
    color: var(--muted);
    letter-spacing: 0.6px;
    margin-top: 4px;
    text-transform: uppercase;
  }
  .contact {
    position: absolute;
    top: 276px;
    left: 36px;
    font-family: "Work Sans", sans-serif;
    font-size: 14px;
    color: var(--ink);
    letter-spacing: 0.6px;
    line-height: 1.55;
  }
  .contact__label, .contact__sep { color: var(--accent); }
  .contact__sep { padding: 0 6px; }
</style>
</head>
<body>
<main class="stage">
  <section class="card card--back" aria-label="Card back">
    <div class="brand">
      <span class="brand__dot" aria-hidden="true"></span>
      <span class="brand__name">Brightlane Exchange</span>
    </div>
  </section>

  <section class="card card--front" aria-label="Card front">
    <div class="brand">
      <span class="brand__dot" aria-hidden="true"></span>
      <span class="brand__name">Brightlane Exchange</span>
    </div>
    <p class="abn"><span class="abn__label">ABN:</span> 38 614 207 923</p>

    <div class="rule rule--top"></div>
    <div class="person">
      <h1 class="person__name">Dale Morven</h1>
      <p class="person__role">|Co-Founder | Managing Director</p>
    </div>
    <div class="rule rule--bottom"></div>

    <div class="contact">
      <p><span class="contact__label">Tel:</span> +61 0487 259 318<span class="contact__sep">|</span>dale.morven@plivorantu.com</p>
      <p>Suite 718 240 Wattlebrook Lane Melbourne Vic 3000</p>
    </div>
  </section>
</main>
</body>
</html>
```